Brightwave Reach - Business Card

We need a business card for a Social Media Marketing company that specializes in online marketing for small businesses in Canada using common Social Media platforms such as Pixlora, Chatterly, Blinkpost & Quibber.

I have uploaded a copy of our logo which I would like utilized in the business card. We would like the business card to be modern yet classy design.

Our website is www.brightwavereach.ca

Industry/Entity Type

Marketing

Contact Information for Business Card

Email: info@brightwavereach.ca
Website: www.brightwavereach.ca
Telephone: 604-555-0193

Colors

Designer to choose colors to be used in the design.

Requirements
Must have
• Social Media icons on reverse
• Please add some designs with color.

```html
<!DOCTYPE html>
<html lang="en">
<head>
<meta charset="UTF-8">
<title>Brightwave Reach – Business Card</title>
<link href="https://fonts.googleapis.com/css2?family=Oswald:wght@400;600&family=Roboto+Condensed:wght@400&display=swap" rel="stylesheet">
<style>
  :root {
    --backdrop: #1f1f20;
    --slate: #4b4f50;
    --slate-dark: #3f4344;
    --paper: #f7f7f6;
    --ink: #4a4d4e;
    --ink-soft: #5d6162;
  }
  * { margin: 0; padding: 0; box-sizing: border-box; }
  html, body { width: 1200px; height: 1000px; overflow: hidden; }
  body {
    background: var(--backdrop);
    position: relative;
    font-family: "Roboto Condensed", sans-serif;
  }
  .card {
    position: absolute;
    top: 348px;
    width: 530px;
    height: 303px;
    overflow: hidden;
    box-shadow: 0 14px 30px rgba(0,0,0,.55);
  }

  /* ---------- Reverse side ---------- */
  .card-back { left: 45px; background: var(--slate); }
  .card-back .band { position: absolute; left: 0; top: 0; width: 530px; height: 303px; }
  .back-brand {
    position: absolute;
    top: 62px; left: 0; width: 100%;
    display: flex; justify-content: center; align-items: center; gap: 12px;
  }
  .back-brand .brand-square {
    width: 16px; height: 16px; background: var(--paper);
  }
  .back-brand .brand-name {
    font-family: "Oswald", sans-serif;
    font-weight: 600;
    font-size: 30px;
    line-height: 1;
    letter-spacing: 1px;
    color: var(--paper);
    text-transform: uppercase;
  }
  .socials {
    position: absolute;
    left: 0; top: 196px; width: 100%;
    display: flex; justify-content: center; gap: 46px;
    list-style: none;
  }
  .social {
    display: flex; flex-direction: column; align-items: center; gap: 8px;
  }
  .social .dot {
    width: 34px; height: 34px; border-radius: 50%;
    background: var(--slate-dark);
    border: 2px solid var(--paper);
  }
  .social .label {
    font-family: "Oswald", sans-serif;
    font-weight: 400;
    font-size: 12px;
    letter-spacing: .5px;
    color: var(--ink);
  }

  /* ---------- Front side ---------- */
  .card-front { left: 625px; background: var(--paper); }
  .front-brand {
    position: absolute;
    left: 34px; top: 62px;
    display: flex; align-items: flex-start; gap: 10px;
  }
  .front-brand .brand-square {
    width: 18px; height: 18px; background: var(--ink); margin-top: 8px;
  }
  .front-brand .brand-name {
    font-family: "Oswald", sans-serif;
    font-weight: 600;
    font-size: 40px;
    line-height: 1.02;
    letter-spacing: 1px;
    color: var(--ink);
    text-transform: uppercase;
  }
  .person {
    position: absolute;
    left: 318px; top: 96px;
  }
  .person .name {
    font-family: "Oswald", sans-serif;
    font-weight: 600;
    font-size: 17px;
    letter-spacing: .5px;
    color: var(--ink);
    text-transform: uppercase;
  }
  .person .role {
    font-family: "Oswald", sans-serif;
    font-weight: 400;
    font-size: 14px;
    color: var(--ink-soft);
    margin-top: -2px;
  }
  .divider {
    position: absolute;
    left: 300px; top: 148px; width: 230px; height: 2px;
    background: var(--ink);
  }
  .contacts {
    position: absolute;
    left: 312px; top: 160px;
    list-style: none;
  }
  .contacts li {
    display: flex; align-items: center; gap: 8px;
    font-size: 13.5px; line-height: 19px;
    color: var(--ink);
  }
  .contacts svg { width: 12px; height: 12px; fill: var(--ink); flex: none; }
  .front-stripe {
    position: absolute; left: 0; width: 100%; background: var(--slate);
  }
  .front-stripe.thin { top: 232px; height: 6px; }
  .front-stripe.wide { top: 246px; height: 57px; }
</style>
</head>
<body>

  <section class="card card-back" aria-label="Business card reverse">
    <svg class="band" viewBox="0 0 530 303" aria-hidden="true">
      <path d="M0 303 V212 H90 Q100 212 106 204 L112 196 Q116 190 124 190 H412 Q420 190 424 196 L430 204 Q436 212 446 212 H530 V303 Z" fill="#f7f7f6"/>
    </svg>
    <div class="back-brand">
      <span class="brand-square"></span>
      <span class="brand-name">Brightwave Reach</span>
    </div>
    <ul class="socials">
      <li class="social"><span class="dot"></span><span class="label">Quibber</span></li>
      <li class="social"><span class="dot"></span><span class="label">Blinkpost</span></li>
      <li class="social"><span class="dot"></span><span class="label">Pixlora</span></li>
      <li class="social"><span class="dot"></span><span class="label">Chatterly</span></li>
    </ul>
  </section>

  <section class="card card-front" aria-label="Business card front">
    <div class="front-brand">
      <span class="brand-square"></span>
      <span class="brand-name">Brightwave<br>Reach</span>
    </div>
    <div class="person">
      <p class="name">Daniel Marsh</p>
      <p class="role">Manager</p>
    </div>
    <div class="divider"></div>
    <ul class="contacts">
      <li>
        <svg viewBox="0 0 24 24"><path d="M6.6 10.8a15.1 15.1 0 0 0 6.6 6.6l2.2-2.2a1 1 0 0 1 1-.25 11.4 11.4 0 0 0 3.6.57 1 1 0 0 1 1 1V20a1 1 0 0 1-1 1A17 17 0 0 1 3 4a1 1 0 0 1 1-1h3.5a1 1 0 0 1 1 1c0 1.25.2 2.45.57 3.57a1 1 0 0 1-.25 1z"/></svg>
        604-555-0193
      </li>
      <li>
        <svg viewBox="0 0 24 24"><path d="M2 5h20v14H2z M4 7v.5l8 5 8-5V7z" fill-rule="evenodd"/></svg>
        info@brightwavereach.ca
      </li>
      <li>
        <svg viewBox="0 0 24 24"><path d="M12 2a10 10 0 1 0 0 20 10 10 0 0 0 0-20zm6.9 6h-2.9a15.6 15.6 0 0 0-1.4-3.6A8 8 0 0 1 18.9 8zM12 4c.8 1.2 1.5 2.5 1.9 4h-3.8c.4-1.5 1.1-2.8 1.9-4zM4.3 14a8 8 0 0 1 0-4h3.4a16 16 0 0 0 0 4zm.8 2h2.9c.3 1.3.8 2.5 1.4 3.6A8 8 0 0 1 5.1 16zM8 8H5.1a8 8 0 0 1 4.3-3.6C8.8 5.5 8.3 6.7 8 8zm4 12c-.8-1.2-1.5-2.5-1.9-4h3.8c-.4 1.5-1.1 2.8-1.9 4zm2.3-6H9.7a14.6 14.6 0 0 1 0-4h4.6a14.6 14.6 0 0 1 0 4zm.3 5.6c.6-1.1 1.1-2.3 1.4-3.6h2.9a8 8 0 0 1-4.3 3.6zM16.3 14a16 16 0 0 0 0-4h3.4a8 8 0 0 1 0 4z"/></svg>
        www.brightwavereach.ca
      </li>
    </ul>
    <div class="front-stripe thin"></div>
    <div class="front-stripe wide"></div>
  </section>

</body>
</html>
```